Website Design Needed for Performance Horse Trading Business

We require a website designed for Saddlewend, a new business which lists top quality performance stock horse bloodlines for sale. Our Australian company caters to the Australian Stock Horse, Quarter Horse and Paint Horse breeds of horse used for performance events such as Camp drafting and Cutting. The website design needs to communicate quality, have a professional look while maintaining a western, rural feel.
Colour schemes that we are looking for are either grey and orange, navy and grey or brown and grey.
The logo for the website has been attached below
Design deliverables are as follows:
-Main Page
-Horses for Sale Page
-Horse Listing Page
-Html & CSS files for pages
MAIN PAGE
----------------
Description: This page is where customers land, search for horses, see premium horses
Elements which need to be included on the main page are
-a horse filter section, allowing customers to search for horse listings by filtering attributes.
-premium listings displaying large photos of horse, price and location.
Horses for Sale PAGE
---------------------------------
Description: This page displays a list of available horses for sale as per the filtered results.
Elements which need to be included on this page are
- a filter panel which allows customers to filter results
- list of horses available for sale
Horse Listing Page
-------------------------------
Description: This page displays all the information about the horse for sale.
Screenshots of the basic program are attached for the Horses for Sale Page and the Horse Listing Page to give an idea of the elements required ONLY and should not be thought of as a design guideline.
Webpage HEADER
-------------------------
The Header section of the website should include login/signup buttons, 'my account' buttons (or links) as well as a featured link/button that says 'Sell Your Horse'
Updates
Thank you all for your designs so far. We would like to see the Sell Your Horse section featured more in the website design to attract customers. This would be as a button or highlighted link that is eye catching in the primary section of the website design of the main page. Perhaps placing it on the right hand side adjacent to the search function lets customers make the mental decision as to whether they are looking to buy or looking to sell when they visit the website. The wording above or near the button would be 'Advertise your horse with us' with the words on the button being 'Create Ad!'.
Industry/Entity Type
Events
Look and feel
Each slider illustrates characteristics of the customer's brand and the style your logo design should communicate.

```html
<!DOCTYPE html>
<html lang="en">
<head>
<meta charset="utf-8">
<title>Saddlewend Australia</title>
<link href="https://fonts.googleapis.com/css2?family=Nunito+Sans:wght@300;400;600&family=Cinzel:wght@700&display=swap" rel="stylesheet">
<style>
:root{
  --orange:#f6a11f;
  --orange-dark:#ee9418;
  --orange-text:#f39a14;
  --grey-bar:#e4e4e4;
  --grey-btn:#7b7b7b;
  --text:#333;
  --muted:#6a6a6a;
  --white:#fff;
  --footer-text:#4a3a1c;
}
*{box-sizing:border-box;margin:0;padding:0}
html,body{width:1053px;height:1200px;overflow:hidden;background:#fff}
body{position:relative;font-family:"Nunito Sans",sans-serif;color:var(--text)}
.abs{position:absolute}
.hero{left:0;top:0;width:1053px;height:497px;
  background:radial-gradient(ellipse at 62% 45%,#c7b9a8 0%,#9a8670 22%,#5f5238 48%,#3b3320 75%,#2a2416 100%)}
.header-band{left:0;top:0;width:1053px;height:103px;background:rgba(150,150,150,.72)}
.brand{left:105px;top:26px;font-family:"Nunito Sans",sans-serif;font-weight:600;font-size:34px;letter-spacing:1px;color:#1b1b1b;display:flex;align-items:center;gap:10px}
.brand-mark{width:16px;height:16px;background:#1b1b1b;border-radius:50%}
.brand-sub{left:146px;top:78px;font-size:9px;letter-spacing:23px;color:#1b1b1b}
.account-pill{left:548px;top:0;width:376px;height:47px;background:#eeeeee;border-radius:0 0 6px 6px;display:flex;align-items:center;padding-left:15px;font-size:14px;color:var(--muted);gap:10px}
.pill-btn{height:32px;border-radius:4px;color:#fff;font-size:15px;display:flex;align-items:center;justify-content:center}
.btn-login{background:var(--grey-btn);width:59px;margin-left:10px}
.btn-signup{background:var(--orange);width:76px}
.nav{top:58px;font-size:16px;color:#fff}
.caption{left:104px;top:214px;width:371px;height:150px;background:rgba(60,55,40,.55);padding:18px 18px}
.caption h1{font-weight:400;font-size:33px;color:var(--orange-text);line-height:1.1}
.caption p{font-size:17px;color:#eee;font-weight:300;line-height:21px;margin-top:6px}
.slider-ctrl{left:884px;top:447px;width:51px;height:36px;background:rgba(40,40,40,.75)}
.search-bar{left:104px;top:497px;width:846px;height:79px;background:var(--grey-bar);border-radius:0 0 5px 5px}
.search-label{left:124px;top:527px;font-size:16px;color:var(--muted);font-weight:300}
.field{top:522px;height:34px;background:#fff;border-radius:3px;font-size:12px;color:var(--muted);display:flex;align-items:center}
.btn{display:flex;align-items:center;justify-content:center;color:#fff;border-radius:4px;font-size:16px}
.welcome{left:0;width:1053px;top:588px;text-align:center;font-size:26px;color:var(--orange-text);font-weight:400}
.intro{left:120px;width:813px;top:630px;text-align:center;font-size:14px;line-height:18px;color:#333}
.section-title{left:111px;top:733px;font-size:21px;color:var(--orange-text)}
.card{top:778px;width:198px;height:244px}
.card-photo{width:198px;height:179px;position:relative;overflow:hidden}
.price{position:absolute;left:9px;top:10px;color:#fff;font-size:14px}
.card-info{height:65px;background:var(--orange);color:#fff;font-size:14px;padding:8px 8px;line-height:23px}
.footer{left:0;top:1036px;width:1053px;height:134px;background:var(--orange)}
.footer-strip{left:0;top:1170px;width:1053px;height:30px;background:var(--orange-dark)}
.foot-h{top:1053px;font-size:13px;font-weight:600;color:var(--footer-text)}
.foot-link{font-size:13px;color:var(--footer-text)}
.social-sq{top:1087px;width:29px;height:29px;border-radius:4px;background:#4a86c5}
.news-input{left:659px;top:1075px;width:226px;height:30px;background:#fff;border-radius:5px;border:1px solid #d9d9d9}
.go{left:889px;top:1073px;width:35px;height:35px;border-radius:50%;background:var(--grey-btn);color:#ddd;font-size:14px;display:flex;align-items:center;justify-content:center}
.news-note{left:659px;top:1114px;width:270px;font-size:10px;font-style:italic;color:#7a5a20;line-height:13px}
.copyright{left:743px;top:1175px;font-size:12px;color:#b8701a}
</style>
</head>
<body>
<div class="abs hero" role="img" aria-label="Close-up photo of a white horse's muzzle in warm evening light"></div>
<div class="abs header-band"></div>
<div class="abs brand"><span>SADDLEWEND</span><span class="brand-mark"></span></div>
<div class="abs brand-sub">AUSTRALIA</div>

<div class="abs account-pill">
  <span>My Account</span><span>|</span><span>Sell Your Horse</span>
  <span class="pill-btn btn-login">Login</span>
  <span class="pill-btn btn-signup">Sign Up</span>
</div>
<span class="abs nav" style="left:493px">Home</span>
<span class="abs nav" style="left:570px">About Us</span>
<span class="abs nav" style="left:670px">Services</span>
<span class="abs nav" style="left:763px">Sell Horse</span>
<span class="abs nav" style="left:867px">Contact</span>

<div class="abs caption">
  <h1>We list</h1>
  <p>showcase top quality performance stock horse bloodlines for sale.</p>
</div>
<div class="abs slider-ctrl">
  <svg width="51" height="36" viewBox="0 0 51 36"><path d="M22 9 L14 18 L22 27 M29 9 L37 18 L29 27" stroke="#fff" stroke-width="2" fill="none"/></svg>
</div>

<div class="abs search-bar"></div>
<span class="abs search-label">Search for horses</span>
<div class="abs field" style="left:276px;width:177px;padding-left:37px">Category
  <svg class="abs" style="left:9px;top:8px" width="20" height="20" viewBox="0 0 20 20"><circle cx="8" cy="8" r="6" stroke="#777" stroke-width="1.6" fill="none"/><path d="M12.5 12.5 L18 18" stroke="#777" stroke-width="2"/></svg>
</div>
<div class="abs field" style="left:461px;width:177px;padding-left:13px">Keywords</div>
<div class="abs btn" style="left:646px;top:522px;width:105px;height:33px;background:var(--grey-btn)">Search</div>
<div class="abs btn" style="left:759px;top:522px;width:176px;height:33px;background:var(--orange)">See Premium horses</div>

<h2 class="abs welcome">Welcome</h2>
<p class="abs intro">Our company caters to the Australian Stock Horse, Quarter Horse and Paint Horse breeds of horse used for performance events such as Camp drafting and Cutting.</p>
<div class="abs btn" style="left:483px;top:681px;width:87px;height:33px;background:var(--orange);color:#5a3a08;font-size:14px">Read more</div>

<h2 class="abs section-title" style="font-weight:400">Premium Listings</h2>
<svg class="abs" style="left:899px;top:747px" width="32" height="22" viewBox="0 0 32 22"><path d="M11 2 L2 11 L11 20 M21 2 L30 11 L21 20" stroke="#777" stroke-width="1.6" fill="none"/></svg>

<div class="abs card" style="left:109px">
  <div class="card-photo" role="img" aria-label="Chestnut stock horse portrait" style="background:linear-gradient(135deg,#d9d9d4,#b0622c 55%,#8a4a22)">
    <svg class="abs" width="78" height="78"><path d="M0 0H78L0 78Z" fill="#6f6f6f" opacity=".85"/></svg><span class="price">$ 750</span></div>
  <div class="card-info">Australian Stock Horse<br>Location : Australia</div>
</div>
<div class="abs card" style="left:320px">
  <div class="card-photo" role="img" aria-label="Bay quarter horse with bridle" style="background:linear-gradient(135deg,#c9c2b3,#9a5228 50%,#5e2f18)">
    <svg class="abs" width="78" height="78"><path d="M0 0H78L0 78Z" fill="#6f6f6f" opacity=".85"/></svg><span class="price">$ 750</span></div>
  <div class="card-info">Quarter Horse<br>Location : Australia</div>
</div>
<div class="abs card" style="left:532px">
  <div class="card-photo" role="img" aria-label="Paint horse in a sunny field" style="background:linear-gradient(135deg,#ece6c9,#7b6a4a 50%,#4a3a2a)">
    <svg class="abs" width="78" height="78"><path d="M0 0H78L0 78Z" fill="#6f6f6f" opacity=".85"/></svg><span class="price">$ 750</span></div>
  <div class="card-info">Paint Horse breeds<br>Location : Australia</div>
</div>
<div class="abs card" style="left:743px">
  <div class="card-photo" role="img" aria-label="Two chestnut horses standing in a pasture" style="background:linear-gradient(135deg,#6f8a4a,#a05a2a 50%,#7a3f1e)">
    <svg class="abs" width="78" height="78"><path d="M0 0H78L0 78Z" fill="#6f6f6f" opacity=".85"/></svg><span class="price">$ 750</span></div>
  <div class="card-info">Paint Horse breeds<br>Location : Australia</div>
</div>

<footer>
  <div class="abs footer"></div>
  <div class="abs footer-strip"></div>
  <span class="abs foot-h" style="left:113px">QUICK LINKS</span>
  <span class="abs foot-link" style="left:114px;top:1085px">Home</span>
  <span class="abs foot-link" style="left:114px;top:1099px;margin-top:1px"></span>
  <span class="abs foot-link" style="left:114px;top:1099px">About Us</span>
  <span class="abs foot-link" style="left:114px;top:1127px">Services</span>
  <span class="abs foot-link" style="left:218px;top:1085px">Sell Horse</span>
  <span class="abs foot-link" style="left:218px;top:1100px">Contact</span>

  <span class="abs foot-h" style="left:404px">FOLLOW US ON</span>
  <div class="abs social-sq" style="left:404px"></div>
  <div class="abs social-sq" style="left:445px"></div>
  <div class="abs social-sq" style="left:485px"></div>
  <span class="abs foot-link" style="left:404px;top:1133px">Fencepost &nbsp;| &nbsp;Chirrup &nbsp;| &nbsp;Worklink</span>

  <span class="abs foot-h" style="left:658px">JOIN US</span>
  <div class="abs news-input">
    <svg class="abs" style="left:9px;top:6px" width="21" height="17" viewBox="0 0 21 17"><rect x="1" y="3" width="19" height="13" fill="#f3e6c6" stroke="#c9a96a"/><path d="M1 3 L10.5 10 L20 3" stroke="#c9a96a" fill="none"/></svg>
  </div>
  <div class="abs go">GO</div>
  <p class="abs news-note">Sed ut perspiciatis unde omnis iste natus error sit voluptatem accusantium doloremque laudantium,</p>
  <span class="abs copyright">© 2013.www.saddlewend-example.com</span>
</footer>
</body>
</html>
```